Fernhill Shopping Centre main sign re-design project

We would like to refresh the look of the main sign we have on the corner of a block of shops to make it more contemproary and vibrant.

A picture of the existing sign which reads Fernhill Shopping Centre can be found in attached PDF and at the following URL.

http://www.quorvelprop.co.nz/~/media/Listings/Region%20Sample/Sample%20City/Sample%20CBD/418206/Images/418206_1.ashx?bc=Gainsboro&as=1&h=550&w=980&ma=1

Fernhill Shopping Centre is also know locally as Fernhill Plaza, but the key word is Fernhill.

The existing signage has a flower/clover pattern on it which I think was just added to create a bit of interest. The building is located in a town surrounded by farm land.

I do quite like the organic feel of plant leaves or certain flowers - preferably New Zealand native plants for instance - the Kowhai flower or leaf block, pohutukawa, or kaka beak - reference images can be found with google image search

Geometric patterns could also be an option.

Once again the imagery is only to soften the sign and add some interest.

Target Market(s)

The target audience is premium shopper

Industry/Entity Type

Building

Requirements
Must have
• Must have the words: Fernhill Shopping Centre.
The big M is not essential, and I would rather the emphasis was on the word Fernhill.
Should not have
• Should not be brown. We want the sign to feel more contemporary, but not too hard. The current pale brown feels too soft in comparison with the look of the building.

```html
<!DOCTYPE html>
<html lang="en">
<head>
<meta charset="utf-8">
<title>Fernhill Shopping Centre – Main Sign</title>
<link rel="stylesheet" href="https://fonts.googleapis.com/css2?family=Archivo:wght@700;800&display=swap">
<style>
  :root {
    --page-bg: #ffffff;
    --sign-face: #ffffff;
    --sign-edge: #b9b9b9;
    --sign-shadow: rgba(0, 0, 0, 0.45);
    --wordmark-green: #1f3f0e;
    --tagline-red: #e31e24;
    --leaf-light: #9cc03a;
    --leaf-dark: #3f6a28;
    --bloom-red: #e31e24;
    --leaf-rust: #a3281f;
  }
  html, body {
    margin: 0;
    padding: 0;
    width: 1200px;
    height: 1000px;
    overflow: hidden;
    background: var(--page-bg);
  }
  .canvas {
    display: block;
    width: 1200px;
    height: 1000px;
  }
  .sign-face {
    fill: var(--sign-face);
    stroke: var(--sign-edge);
    stroke-width: 1;
  }
  .sign-shadow {
    fill: var(--sign-shadow);
  }
  .wordmark {
    font-family: "Archivo", "Arial Black", sans-serif;
    font-weight: 800;
    font-size: 118px;
    fill: var(--wordmark-green);
  }
  .tagline {
    font-family: "Archivo", Arial, sans-serif;
    font-weight: 700;
    font-size: 44px;
    fill: var(--tagline-red);
  }
</style>
</head>
<body>
<svg class="canvas" viewBox="0 0 1200 1000" xmlns="http://www.w3.org/2000/svg">
  <defs>
    <linearGradient id="foliage-tone" x1="0" y1="0" x2="1" y2="1">
      <stop offset="0" stop-color="var(--leaf-light)"/>
      <stop offset="0.4" stop-color="var(--leaf-dark)"/>
      <stop offset="0.7" stop-color="var(--bloom-red)"/>
      <stop offset="1" stop-color="var(--leaf-rust)"/>
    </linearGradient>
    <linearGradient id="foliage-fade" x1="0" y1="0" x2="0" y2="1">
      <stop offset="0" stop-color="#ffffff" stop-opacity="1"/>
      <stop offset="0.35" stop-color="#ffffff" stop-opacity="0"/>
    </linearGradient>
    <filter id="panel-blur" x="-5%" y="-5%" width="110%" height="110%">
      <feGaussianBlur stdDeviation="2"/>
    </filter>
  </defs>

  <g class="sign">
    <rect class="sign-shadow" x="416" y="116" width="377" height="753" filter="url(#panel-blur)"/>
    <rect class="sign-face" x="412.5" y="112.5" width="377" height="753"/>

    <text class="wordmark" x="428" y="320" textLength="350" lengthAdjust="spacingAndGlyphs">FERNHILL</text>
    <text class="tagline" x="430" y="383" textLength="340" lengthAdjust="spacingAndGlyphs">Shopping Centre</text>

    <g class="foliage-band" role="img" aria-label="Illustration of pohutukawa blossoms and native leaves in greens and reds along the base of the sign">
      <rect x="413" y="598" width="376" height="267" fill="url(#foliage-tone)"/>
      <rect x="413" y="598" width="376" height="267" fill="url(#foliage-fade)"/>
    </g>
  </g>
</svg>
</body>
</html>
```